Medical centre needs a business card

We are a medcial centre in Australia, needing a new business card. Our demographic is low working class families. We are going to be renovating our premises to modernise the look and also had a new logo done a few months ago representing quality and community, and now need to update our cards. It needs to be doubled sided, with logo and contact details on the front, and appointment details on the back. . Needs to be modern and simple, easy to read. <br/><br/>Name: Kindle Grove Medical Centre <br/>Address: 512 Parmley Rd (Cnr Parmley Rd & Osgood Creek Rd),<br/>Tindarra Court Shopping Centre, Paralowie, SA 5108<br/>Ph: 08 8461 3072<br/>Tag line: Where your wellbeing comes first<br/>Website: www.kindlegrovemedicalcentre-example.com.au<br/>Online bookings also available<br/><br/>(On the back, to have 3 lines of appointments that can be written in.<br/>Day, date, time)<br/><br/>Your next appointment is on<br/>Can try “M T W Th F Sa Su _________________ at ____________ am/pm” or other combinations <br/>Please advise as soon as possible if unable to attend<br/>Cancellation fees apply if less than 2 hrs notice<br/>Online appointments available (please highlight this option by either by position, colour or font)

Target Market(s)

Lower social economic working class, young families to seniors

Industry/Entity Type

Medical Centre

Contact Information for Business Card

Kindle Grove Medical Centre
512 Parmley Rd (Cnr Parmley Rd & Osgood Creek Drive)
Tindarra Court Shopping Centre
Bellmere SA 5290
Ph: 08 8461 3072
www.kindlegrovemedicalcentre-example.com.au
Tagline line: where your wellbeing comes first
Back side is for appointments
Your next appointment is with Dr ______________
Day/date/time (Please give 3 lines of appointments)
Please advise as soon as possible if unable to attend
Cancellation fees apply if less than 2 hours notice
Online appointments available
Book online easily and conveniently (please highlight online appointments)

Font styles to use
Serif
Sans Serif

Colors

Designer to choose colors to be used in the design.

Requirements
Must have
• Modern and simple
• Easy to ready
• Induces a wellbeing feeling
• Incorporate our logo colours and feel from logo
• Induces feeling of stability and security
Nice to have
• Attract attention
• Pleasant to look at
• Feeling of innovation
Should not have
• Loud clashing colours
• Overly luxurious feeling
• Overly artistic

```html
<!DOCTYPE html>
<html lang="en">
<head>
<meta charset="utf-8">
<title>Kindle Grove Medical Centre – Business Card</title>
<link href="https://fonts.googleapis.com/css2?family=Work+Sans:wght@400;500;600&display=swap" rel="stylesheet">
<style>
  :root {
    --backdrop: #2a2a2a;
    --card: #ffffff;
    --brand-blue: #1a72c4;
    --brand-blue-light: #2c9be0;
    --brand-green: #8dc63f;
    --text-grey: #6b6b6b;
    --rule-grey: #8a8a8a;
  }
  * { margin: 0; padding: 0; box-sizing: border-box; }
  html, body {
    width: 1200px; height: 900px; overflow: hidden;
    background: var(--backdrop);
    font-family: "Work Sans", Arial, sans-serif;
  }
  .card {
    position: absolute; left: 261px; width: 656px; height: 357px;
    background: var(--card); border-radius: 26px; overflow: hidden;
    text-align: center; color: var(--text-grey);
  }
  .card--front { top: 69px; }
  .card--back { top: 472px; }

  /* front */
  .brand {
    position: absolute; top: 82px; left: 0; right: 0;
    display: flex; justify-content: center; align-items: center; gap: 14px;
  }
  .brand__dot { width: 44px; height: 44px; border-radius: 50%; background: var(--brand-green); }
  .brand__name {
    color: var(--brand-blue); font-weight: 600; font-size: 30px;
    line-height: 1.1; text-transform: uppercase; text-align: left; letter-spacing: .5px;
  }
  .tagline {
    position: absolute; top: 168px; left: 0; right: 0;
    font-size: 12px; letter-spacing: 1.2px; text-transform: uppercase;
  }
  .divider { position: absolute; top: 198px; left: 0; width: 656px; height: 26px; }
  .contact {
    position: absolute; left: 0; right: 0;
    font-weight: 500; font-size: 15px; letter-spacing: 1px; line-height: 20px;
  }
  .contact--phone { top: 238px; }
  .contact--web { top: 258px; }
  .contact--address { top: 288px; }
  .base-band {
    position: absolute; left: 0; right: 0; bottom: 0; height: 16px;
    border-top: 3px solid var(--brand-green);
    background: linear-gradient(90deg, var(--brand-blue), var(--brand-blue-light));
  }

  /* back */
  .back-title {
    position: absolute; top: 34px; left: 0; right: 0;
    color: var(--brand-blue); font-weight: 600; font-size: 28px;
    text-transform: uppercase; letter-spacing: 1px;
  }
  .back-rule {
    position: absolute; top: 78px; left: 144px; width: 368px; height: 3px; background: var(--brand-blue);
  }
  .appointment {
    position: absolute; left: 104px; width: 450px;
    text-align: left; font-size: 16px; letter-spacing: .8px;
  }
  .appointment--doctor { top: 118px; color: var(--brand-blue); font-weight: 500; }
  .appointment--day { top: 158px; }
  .appointment--date { top: 198px; }
  .appointment--time { top: 238px; }
  .field { display: flex; align-items: flex-end; gap: 6px; }
  .field__line { flex: 1; border-bottom: 1px solid var(--rule-grey); height: 14px; }
  .field__line--short { flex: 0 0 134px; border-color: var(--brand-blue); }
  .notice {
    position: absolute; top: 280px; left: 0; right: 0;
    font-size: 16px; letter-spacing: 1.2px; line-height: 20px;
  }
  .notice__online { color: var(--brand-green); font-weight: 500; font-size: 17px; }
</style>
</head>
<body>

<section class="card card--front">
  <div class="brand">
    <span class="brand__dot"></span>
    <h1 class="brand__name">Kindle Grove<br>Medical Centre</h1>
  </div>
  <p class="tagline">Where your wellbeing comes first</p>

  <svg class="divider" viewBox="0 0 656 26" aria-hidden="true">
    <line x1="0" y1="13" x2="290" y2="13" stroke="#1a72c4" stroke-width="1.5"/>
    <line x1="366" y1="13" x2="656" y2="13" stroke="#1a72c4" stroke-width="1.5"/>
    <circle cx="309" cy="13" r="11.5" fill="#fff" stroke="#8dc63f" stroke-width="1.5"/>
    <path d="M304.5 7.5c1-.6 1.8-.4 2.3.5l1 1.9c.4.8.2 1.4-.5 1.9l-.6.4c.4 1.6 1.3 3 2.6 4l.6-.3c.7-.4 1.4-.3 1.9.4l1.2 1.6c.5.8.3 1.6-.6 2.1-3.5 1.7-8.5-5.2-7.9-12.5z" fill="#1a72c4"/>
    <circle cx="347" cy="13" r="11.5" fill="#fff" stroke="#8dc63f" stroke-width="1.5"/>
    <g fill="none" stroke="#1a72c4" stroke-width="1">
      <circle cx="347" cy="13" r="6.5"/>
      <ellipse cx="347" cy="13" rx="2.8" ry="6.5"/>
      <line x1="340.5" y1="13" x2="353.5" y2="13"/>
      <line x1="341.5" y1="9.5" x2="352.5" y2="9.5"/>
      <line x1="341.5" y1="16.5" x2="352.5" y2="16.5"/>
    </g>
  </svg>

  <p class="contact contact--phone">08 8461 3072</p>
  <p class="contact contact--web">www.kindlegrovemedicalcentre-example.com.au</p>
  <p class="contact contact--address">512 Parmley Rd (Cnr Parmley Rd &amp; Osgood Creek Drive)<br>Tindarra Court Shopping Centre Bellmere SA 5290</p>
  <div class="base-band"></div>
</section>

<section class="card card--back">
  <h2 class="back-title">Kindle Grove Medical Centre</h2>
  <div class="back-rule"></div>

  <p class="appointment appointment--doctor field">Your next appointment is with Dr <span class="field__line field__line--short"></span></p>
  <p class="appointment appointment--day field">Day <span class="field__line"></span></p>
  <p class="appointment appointment--date field">date <span class="field__line"></span></p>
  <p class="appointment appointment--time field">time <span class="field__line"></span></p>

  <p class="notice">
    Please advise as soon as possible if unable to attend<br>
    Cancellation fees apply if less than 2 hours notice<br>
    <span class="notice__online">Online appointments available.</span>
  </p>
</section>

</body>
</html>
```